RTavenor Business Cards & Letterhead

I have a logo but need a design for some new business cards. We are a Design-Build Firm that specializes in the design and construction of commercial projects.
the cards need to be professional. no cartoon stuff.
i would like to have the cards in AI format so I can update the card as needed. Logo is provided.
Our Address is: 4187 Marlowe Ct. Apex, North Carolina 27614

```html
<!DOCTYPE html>
<html lang="en">
<head>
<meta charset="utf-8">
<title>RTavenor Business Cards</title>
<link href="https://fonts.googleapis.com/css2?family=Montserrat:wght@500;700&family=Lato:wght@400&display=swap" rel="stylesheet">
<style>
  :root {
    --stage: #1c1c1c;
    --card-dark: #2a2a2a;
    --white: #ffffff;
    --blue: #0a6db3;
    --blue-deep: #0b4f8c;
    --blue-light: #1a86cc;
    --ink: #2b2b2b;
  }
  * { margin: 0; padding: 0; box-sizing: border-box; }
  html, body { width: 1200px; height: 875px; overflow: hidden; }
  body {
    background: var(--stage);
    position: relative;
    font-family: "Lato", Arial, sans-serif;
  }
  .card {
    position: absolute;
    width: 580px;
    height: 330px;
    overflow: hidden;
  }
  /* Back card */
  .card-back {
    left: 70px; top: 90px;
    background: var(--card-dark);
    border-bottom-left-radius: 150px;
    display: flex; align-items: center; justify-content: center; gap: 18px;
  }
  .brand-square {
    width: 40px; height: 40px;
    background: var(--blue);
  }
  .brand-name {
    font-family: "Montserrat", Arial, sans-serif;
    font-weight: 700;
    font-size: 64px;
    letter-spacing: 1px;
    color: var(--white);
  }
  /* Front card */
  .card-front {
    left: 550px; top: 470px;
    background: var(--white);
    border-top-right-radius: 60px;
  }
  .name-band {
    position: absolute; left: 0; top: 0;
    width: 360px; height: 110px;
    background: var(--card-dark);
    padding: 34px 0 0 36px;
  }
  .person-name {
    font-family: "Montserrat", Arial, sans-serif;
    font-weight: 700;
    font-size: 26px;
    color: var(--white);
    text-transform: uppercase;
    line-height: 1;
  }
  .person-title {
    font-family: "Montserrat", Arial, sans-serif;
    font-weight: 500;
    font-size: 17px;
    color: var(--blue);
    margin-top: 6px;
  }
  .accent-panel {
    position: absolute; right: 0; top: 0;
    width: 210px; height: 330px;
    background: linear-gradient(160deg, var(--blue-light), var(--blue-deep));
  }
  .contact-list {
    position: absolute; left: 40px; top: 140px;
    list-style: none;
    font-size: 15px;
    color: var(--ink);
    line-height: 24px;
  }
  .contact-list li { display: flex; align-items: flex-start; gap: 10px; }
  .contact-list svg { width: 14px; height: 14px; margin-top: 5px; flex: none; fill: var(--blue); }
</style>
</head>
<body>
  <section class="card card-back">
    <span class="brand-square"></span>
    <span class="brand-name">RTavenor</span>
  </section>

  <section class="card card-front">
    <div class="name-band">
      <div class="person-name">Daniel Hartwell</div>
      <div class="person-title">Founder &amp; CEO</div>
    </div>
    <div class="accent-panel"></div>
    <ul class="contact-list">
      <li><svg viewBox="0 0 16 16"><path d="M3 1l3 3-2 2c1 2 3 4 5 5l2-2 3 3-2 3C6 15 1 10 1 3z"/></svg>(919) 555-0142</li>
      <li><svg viewBox="0 0 16 16"><path d="M4 0h8v16H4zM5.5 2v10h5V2zM7 13h2v1.5H7z"/></svg>(919) 555-0178</li>
      <li><svg viewBox="0 0 16 16"><path d="M4 1h8v4H4zM1 6h14v7h-3v2H4v-2H1zM5 10v4h6v-4z"/></svg>(919) 555-0193</li>
      <li><svg viewBox="0 0 16 16"><path d="M0 3h16v10H0zM1.5 4.5L8 9l6.5-4.5"/></svg>office@rtavenorbuild.com</li>
      <li><svg viewBox="0 0 16 16"><path d="M8 0a8 8 0 100 16A8 8 0 008 0zm0 2a6 6 0 110 12A6 6 0 018 2zM7 3v10h2V3z"/></svg>www.rtavenorbuild.com</li>
      <li><svg viewBox="0 0 16 16"><path d="M8 0a5.5 5.5 0 00-5.5 5.5C2.5 10 8 16 8 16s5.5-6 5.5-10.5A5.5 5.5 0 008 0zm0 3.5a2 2 0 110 4 2 2 0 010-4z"/></svg>4187 Marlowe Ct. Apex<br>North Carolina 27614</li>
    </ul>
  </section>
</body>
</html>
```